Design NEW business card

We would like a business card using the colour deep red wine or dark navy blue textured background (patterned or not, open to suggestions) with a high gloss debossed rose gold/copper RM Roland Mercer Jewellery business name (Provided). I have included images for your review we would like to keep our currently logo and business name on the front but you can change the layout and positioning. For the back of the card we are open to all suggestions/variations.
Business
Use our current RM Roland Mercer Jewellery logo (Provided image)

```html
<!DOCTYPE html>
<html lang="en">
<head>
<meta charset="utf-8">
<title>Roland Mercer Jewellery – Business Card</title>
<link href="https://fonts.googleapis.com/css2?family=Montserrat:wght@400&family=Oswald:wght@500&family=Roboto:wght@400&display=swap" rel="stylesheet">
<style>
  :root {
    --backdrop: #cbcbcb;
    --wine: #56202a;
    --gold-light: #dcae8d;
    --gold-mid: #b8876a;
    --gold-dark: #8e6550;
    --ink-light: #fbf3ee;
  }
  * { margin: 0; padding: 0; box-sizing: border-box; }
  html, body { width: 1200px; height: 960px; overflow: hidden; }
  body {
    position: relative;
    background: var(--backdrop);
    font-family: "Roboto", Arial, sans-serif;
  }
  .card {
    position: absolute;
    left: 320px;
    width: 600px;
    height: 342px;
    overflow: hidden;
  }
  .gold-surface {
    background: radial-gradient(ellipse 60% 75% at 50% 45%, var(--gold-light) 0%, var(--gold-mid) 55%, var(--gold-dark) 100%);
  }

  /* Front */
  .card-front { top: 105px; }
  .brand {
    position: absolute;
    left: 0; right: 0;
    top: 195px;
    text-align: center;
    font-family: "Montserrat", Arial, sans-serif;
    font-weight: 400;
    color: var(--ink-light);
    font-size: 20px;
    letter-spacing: 5px;
    text-transform: uppercase;
  }
  .front-web {
    position: absolute;
    left: 0; right: 0;
    top: 295px;
    text-align: center;
    color: var(--ink-light);
    font-size: 13px;
    letter-spacing: 5px;
  }

  /* Back */
  .card-back { top: 493px; background: var(--wine); }
  .info-band {
    position: absolute;
    left: 0; right: 0;
    top: 100px;
    height: 142px;
  }
  .identity {
    position: absolute;
    right: 330px;
    top: 45px;
    text-align: right;
    color: var(--ink-light);
  }
  .identity-name {
    font-family: "Oswald", "Arial Narrow", sans-serif;
    font-weight: 500;
    font-size: 28px;
    line-height: 30px;
  }
  .identity-role { font-size: 14px; margin-top: 2px; }
  .divider {
    position: absolute;
    left: 300px;
    top: 16px;
    width: 2px;
    height: 106px;
    background: var(--ink-light);
  }
  .contacts {
    position: absolute;
    left: 328px;
    top: 24px;
    list-style: none;
    color: var(--ink-light);
    font-size: 14px;
  }
  .contacts li {
    display: flex;
    align-items: center;
    height: 19px;
  }
  .contacts svg { width: 14px; height: 14px; margin-right: 8px; fill: var(--ink-light); }
  .address {
    position: absolute;
    left: 0; right: 0;
    top: 288px;
    text-align: center;
    color: var(--ink-light);
    font-size: 14px;
  }
</style>
</head>
<body>

<section class="card card-front gold-surface">
  <div class="brand">Roland Mercer Jewellery</div>
  <div class="front-web">www.rmjewel.com</div>
</section>

<section class="card card-back">
  <div class="info-band gold-surface">
    <div class="identity">
      <div class="identity-name">OWEN HARTLEY</div>
      <div class="identity-role">CEO/FOUNDER</div>
    </div>
    <div class="divider"></div>
    <ul class="contacts">
      <li><svg viewBox="0 0 16 16"><path d="M3 1l3 3-1.5 2c1 2 3.5 4.5 5.5 5.5L12 10l3 3-2 2C7 15 1 9 1 3z"/></svg>555 210 4817</li>
      <li><svg viewBox="0 0 16 16"><path d="M4 0h8v16H4zM5.5 2v10h5V2zM7 13.2h2v1.3H7z" fill-rule="evenodd"/></svg>555 372 9046</li>
      <li><svg viewBox="0 0 16 16"><path d="M4 1h8v4H4zM1 6h14v7h-3v2H4v-2H1zM5 10v4h6v-4z" fill-rule="evenodd"/></svg>555 648 2193</li>
      <li><svg viewBox="0 0 16 16"><path d="M1 4h14v9H1zM2 5l6 4 6-4z" fill-rule="evenodd"/></svg>hello@rmjewel.com</li>
      <li><svg viewBox="0 0 16 16"><path d="M8 1a7 7 0 100 14A7 7 0 008 1zM5 4c2 1 1 3 3 4s0 4 2 5c-3 1-7-1-7-5 0-2 1-3 2-4zm5-1c2 1 3 3 2 5-1-1-2-2-2-5z" fill-rule="evenodd"/></svg>www.rmjewel.com</li>
    </ul>
  </div>
  <div class="address">2140 Linden Court, Fairview, Oregon 97024</div>
</section>

</body>
</html>
```